Tech business card design

We need an amazing business card design for our new business 'Pexla' a marketing tech startup based in Sydney, Australia. We provide an online marketplace for businesses to search and buy advertising media, connect with service providers and learn more about marketing. We wish to communicate 'cool tech', reliability and professionalism and design based around our logo.

Target Market(s)

Business Owners

Contact Information for Business Card

Name
Position
Email Address
Website
Phone Number

Font styles to use
Other font styles liked:
• Avenir & Avenir Next

Colors

Designer to choose colors to be used in the design.

```html
<!DOCTYPE html>
<html lang="en">
<head>
<meta charset="utf-8">
<title>Pexla Business Card</title>
<link rel="stylesheet" href="https://fonts.googleapis.com/css2?family=Mulish:wght@400;700;900&display=swap">
<style>
  :root {
    --backdrop: #2a2a2c;
    --card-white: #ffffff;
    --navy: #1f2452;
    --grey: #6b6c6f;
    --grey-light: #8a8b8e;
    --ink: #222226;
  }
  * { margin: 0; padding: 0; box-sizing: border-box; }
  html, body { width: 1200px; height: 900px; overflow: hidden; background: var(--backdrop); }
  body { position: relative; font-family: "Mulish", "Avenir Next", sans-serif; }

  .card {
    position: absolute;
    width: 560px;
    height: 320px;
    border-radius: 28px;
    overflow: hidden;
    box-shadow: 0 14px 30px rgba(0,0,0,0.45);
  }
  .card-front { left: 120px; top: 110px; background: var(--card-white); }
  .card-back { left: 520px; top: 470px; background: var(--grey); }

  .front-bands { position: absolute; inset: 0; }

  .wordmark {
    font-family: "Mulish", "Avenir Next", sans-serif;
    font-weight: 900;
    color: var(--navy);
    letter-spacing: -0.02em;
    line-height: 1;
  }
  .front-wordmark { position: absolute; right: 42px; top: 28px; font-size: 72px; }
  .back-wordmark {
    position: absolute; left: 0; right: 0; top: 50%;
    transform: translateY(-50%);
    text-align: center; font-size: 150px;
  }

  .name-block {
    position: absolute; left: 0; top: 120px;
    padding-left: 34px;
  }
  .name-marker {
    position: absolute; left: 10px; top: 6px;
    width: 12px; height: 32px; background: var(--grey-light);
  }
  .person-name { font-weight: 900; font-size: 19px; color: var(--navy); letter-spacing: 0.02em; }
  .person-role { font-weight: 700; font-size: 15px; color: var(--ink); }

  .contact-list {
    position: absolute; left: 34px; top: 186px;
    list-style: none; font-size: 15px; color: var(--ink);
  }
  .contact-list li { display: flex; align-items: center; gap: 6px; line-height: 22px; }
  .contact-list svg { width: 13px; height: 13px; fill: var(--ink); }

  .address { position: absolute; left: 52px; top: 244px; font-size: 14px; line-height: 17px; color: var(--ink); }

  .website {
    position: absolute; right: 26px; top: 184px;
    font-size: 14px; line-height: 18px; color: var(--card-white); letter-spacing: 0.14em;
  }
</style>
</head>
<body>
  <section class="card card-front" aria-label="Business card front">
    <svg class="front-bands" viewBox="0 0 560 320" width="560" height="320" aria-hidden="true">
      <path d="M0 298 H300 Q325 298 340 284 L380 196 Q388 176 410 176 H560 V320 H0 Z" fill="var(--navy)"/>
      <path d="M0 306 H310 Q335 306 350 292 L392 222 Q400 210 420 210 H560 V320 H0 Z" fill="var(--grey)"/>
    </svg>

    <div class="wordmark front-wordmark">pexla</div>

    <div class="name-block">
      <span class="name-marker"></span>
      <p class="person-name">JOHN SMITH</p>
      <p class="person-role">Position</p>
    </div>

    <ul class="contact-list">
      <li>
        <svg viewBox="0 0 24 24"><path d="M6.6 10.8c1.4 2.8 3.8 5.1 6.6 6.6l2.2-2.2c.3-.3.7-.4 1-.2 1.1.4 2.300.6 3.6.6.6 0 1 .4 1 1V20c0 .6-.4 1-1 1C10.6 21 3 13.4 3 4c0-.6.4-1 1-1h3.5c.6 0 1 .4 1 1 0 1.3.2 2.5.6 3.6.1.3 0 .7-.2 1z"/></svg>
        012-345-6789
      </li>
      <li>
        <svg viewBox="0 0 24 24"><path d="M2 5h20v14H2z M4 7v.5l8 5 8-5V7z" fill-rule="evenodd"/></svg>
        info@pexla.com
      </li>
    </ul>

    <p class="address">Street Name, City Name<br>Zipcode:012345</p>

    <p class="website">www.pexla.com</p>
  </section>

  <section class="card card-back" aria-label="Business card back">
    <div class="wordmark back-wordmark">pexla</div>
  </section>
</body>
</html>
```